Stylish Business Cards Wanted

- DOUBLE SIDED Design Required -

High end, edgy cards for a corporate and personal stylist. Must include logo,
Name: Belinda Harwick
Title: Director and Stylist
telephone : +61 8 7142 5809
email: belinda@theloombriefing.example
website: theloombriefing.example
Tag: Corporate Workwear & Uniform Specialist | Personal Stylist
Would like nice icons for telephone, email, website

Target Market(s)

Businesses wanting stylish uniforms, people wanting stylish wardrobes

Industry/Entity Type

Corporate Workwear Stylist

Contact Information for Business Card

I would like black, white and gold foiling incorporated in the design - possibly a touch of the other colours on my branding guide attached Name: Belinda Harwick Title: Director and Stylist telephone : +61 8 7142 5809 email: belinda@theloombriefing.example website: theloombriefing.example Tag: Corporate Workwear & Uniform Specialist | Personal Stylist Would like nice icons for telephone, email, website

Font styles to use
Other font styles liked:
• Raleway

Colors

Designer to choose colors to be used in the design.

Requirements
Must have
• Gold foil accents

```html
<!DOCTYPE html>
<html lang="en">
<head>
<meta charset="utf-8">
<title>The Loom Briefing — Business Card</title>
<link rel="stylesheet" href="https://fonts.googleapis.com/css2?family=Raleway:wght@400;500&display=swap">
<style>
  :root {
    --magenta: #c8167a;
    --magenta-soft: #d2338b;
    --ink: #1d2342;
    --gold: #c9a44c;
    --paper: #f4f4f4;
    --stage: #e9e6e8;
    --white: #ffffff;
  }
  * { box-sizing: border-box; margin: 0; padding: 0; }
  html, body {
    width: 1200px; height: 960px; overflow: hidden;
    background: var(--stage);
    font-family: "Raleway", sans-serif;
  }
  .sheet {
    width: 1200px; height: 960px;
    display: flex; flex-direction: column;
    align-items: center; justify-content: center; gap: 36px;
  }
  .card {
    position: relative;
    width: 760px; height: 434px;
    border-radius: 36px;
    overflow: hidden;
    box-shadow: 0 10px 30px rgba(60, 20, 45, 0.18);
  }

  /* Front */
  .card--front { background: var(--magenta); color: var(--white); }
  .front-texture {
    position: absolute; inset: 0;
    background: radial-gradient(ellipse 60% 90% at 62% 40%, var(--magenta-soft) 0%, rgba(210, 51, 139, 0) 70%);
  }
  .front-brand {
    position: absolute; left: 0; right: 0; top: 130px;
    display: flex; align-items: center; justify-content: center; gap: 16px;
  }
  .front-brand-mark {
    width: 16px; height: 16px; background: var(--gold); flex: none;
  }
  .front-brand-name {
    font-weight: 500; font-size: 46px; letter-spacing: 2px; color: var(--white);
    white-space: nowrap;
  }
  .front-tagline {
    position: absolute; left: 0; right: 0; bottom: 64px;
    text-align: center;
    font-weight: 400; font-size: 21px; letter-spacing: 1px;
    white-space: nowrap;
  }

  /* Back */
  .card--back { background: var(--paper); color: var(--ink); }
  .back-brand {
    position: absolute; top: 54px; right: 58px;
    display: flex; align-items: center; gap: 10px;
  }
  .back-brand-mark { width: 12px; height: 12px; background: var(--gold); flex: none; }
  .back-brand-name {
    font-weight: 500; font-size: 26px; letter-spacing: 1px; color: var(--ink);
    white-space: nowrap;
  }
  .identity { position: absolute; left: 64px; top: 180px; }
  .identity-name {
    font-size: 31px; font-weight: 400; letter-spacing: 0.5px;
    padding-bottom: 4px;
    border-bottom: 1.5px solid var(--ink);
    display: inline-block;
    white-space: nowrap;
  }
  .identity-name .first { color: var(--magenta); font-weight: 500; }
  .identity-title { font-size: 17px; margin-top: 6px; }

  .contacts {
    position: absolute; left: 64px; right: 54px; bottom: 58px;
    display: flex; justify-content: space-between; align-items: center;
    list-style: none;
  }
  .contact {
    display: flex; align-items: center; gap: 10px;
    font-size: 14px; white-space: nowrap;
  }
  .contact-icon {
    width: 26px; height: 26px; border-radius: 6px;
    background: var(--magenta);
    display: flex; align-items: center; justify-content: center;
    flex: none;
  }
  .contact-icon svg { width: 16px; height: 16px; }
</style>
</head>
<body>
<main class="sheet">

  <section class="card card--front" aria-label="Card front">
    <div class="front-texture" role="img" aria-label="Faint oversized brand lettering in a lighter magenta tone"></div>
    <div class="front-brand">
      <span class="front-brand-mark"></span>
      <span class="front-brand-name">The Loom Briefing</span>
    </div>
    <p class="front-tagline">Corporate Workwear &amp; Uniform Specialist</p>
  </section>

  <section class="card card--back" aria-label="Card back">
    <div class="back-brand">
      <span class="back-brand-mark"></span>
      <span class="back-brand-name">The Loom Briefing</span>
    </div>

    <div class="identity">
      <h1 class="identity-name"><span class="first">BELINDA</span> HARWICK</h1>
      <p class="identity-title">Director &amp; Stylist</p>
    </div>

    <ul class="contacts">
      <li class="contact">
        <span class="contact-icon">
          <svg viewBox="0 0 24 24" fill="none" stroke="#fff" stroke-width="2" stroke-linecap="round" stroke-linejoin="round">
            <path d="M6 3h3l2 5-2.5 1.5a11 11 0 0 0 6 6L16 13l5 2v3a2 2 0 0 1-2 2A17 17 0 0 1 4 5a2 2 0 0 1 2-2z"/>
          </svg>
        </span>
        +61 8 7142 5809
      </li>
      <li class="contact">
        <span class="contact-icon">
          <svg viewBox="0 0 24 24" fill="none" stroke="#fff" stroke-width="2" stroke-linejoin="round">
            <rect x="3" y="6" width="18" height="12" rx="1.5"/>
            <path d="M3 7l9 6 9-6"/>
          </svg>
        </span>
        belinda@theloombriefing.example
      </li>
      <li class="contact">
        <span class="contact-icon">
          <svg viewBox="0 0 24 24" fill="none" stroke="#fff" stroke-width="1.8">
            <circle cx="12" cy="12" r="9"/>
            <ellipse cx="12" cy="12" rx="4" ry="9"/>
            <path d="M3 12h18M5 7.5h14M5 16.5h14"/>
          </svg>
        </span>
        theloombriefing.example
      </li>
    </ul>
  </section>

</main>
</body>
</html>
```